KDWB Business Card

Looking for a business card design to incorporate our branding. We want to only use the colors listing in the Branding Package (attached).
Updates

Target Market(s)

People who need their phone or device fixed.

Industry/Entity Type

Electronics

Contact Information for Business Card

Please use:

Brightwick Gadget Clinic LLC
4810 E Harlow Ridge Rd
Suite 417
San Antonio, TX 78163

Marcus Delgrove, Store Manager

(210) 555-0147

Requirements
Must have
• Must include the colors that are contained within the Branding Package PDF file.

```html
<!DOCTYPE html>
<html lang="en">
<head>
<meta charset="utf-8">
<title>Brightwick Gadget Clinic – Business Card</title>
<link href="https://fonts.googleapis.com/css2?family=Arimo:wght@400;700&display=swap" rel="stylesheet">
<style>
  :root {
    --page-bg: #3a322e;
    --card-bg: #1d1d1d;
    --brand-orange: #f05a1e;
    --text-light: #ececec;
    --text-muted: #8a8a8a;
    --divider: #5a5a5a;
  }
  * { margin: 0; padding: 0; box-sizing: border-box; }
  html, body {
    width: 1200px; height: 764px; overflow: hidden;
    background: var(--page-bg);
    font-family: "Arimo", Arial, sans-serif;
  }
  .canvas {
    width: 1200px; height: 764px;
    display: flex; align-items: center; justify-content: center; gap: 60px;
  }
  .card {
    width: 520px; height: 297px;
    background: var(--card-bg);
    border-radius: 4px;
    position: relative;
    box-shadow: 0 10px 30px rgba(0,0,0,.45);
  }
  .brand {
    display: flex; align-items: center; gap: 12px;
  }
  .brand-square {
    width: 34px; height: 34px; flex: none;
    background: var(--brand-orange);
    border-radius: 4px;
  }
  .brand-name {
    color: var(--brand-orange);
    font-size: 21px; font-weight: 400; line-height: 1.15;
  }
  /* back: brand + contact */
  .card-back .brand {
    position: absolute; left: 34px; top: 176px; width: 220px;
  }
  .card-back .brand-name { font-size: 18px; }
  .divider {
    position: absolute; left: 280px; top: 48px; bottom: 48px;
    width: 1px; background: var(--divider);
  }
  .contact {
    position: absolute; left: 308px; top: 62px; right: 20px;
    color: var(--text-light);
  }
  .person-name { font-size: 15px; }
  .person-title { font-size: 9px; color: var(--brand-orange); margin-top: 3px; }
  .contact-row {
    display: flex; align-items: flex-start; gap: 8px;
    font-size: 11px; line-height: 1.35; margin-top: 24px;
  }
  .contact-row svg { flex: none; margin-top: 1px; }
  /* front: brand only */
  .card-front .brand {
    position: absolute; left: 50%; top: 50%;
    transform: translate(-50%, -50%);
  }
  .card-front .brand-square { width: 44px; height: 44px; }
  .card-front .brand-name { font-size: 26px; white-space: nowrap; }
</style>
</head>
<body>
<main class="canvas">
  <section class="card card-back">
    <div class="brand">
      <span class="brand-square"></span>
      <span class="brand-name">Brightwick Gadget Clinic</span>
    </div>
    <div class="divider"></div>
    <div class="contact">
      <p class="person-name">Marcus Delgrove</p>
      <p class="person-title">Store Manager</p>
      <div class="contact-row">
        <svg width="12" height="12" viewBox="0 0 12 12" aria-hidden="true">
          <rect width="12" height="12" fill="var(--brand-orange)"/>
          <path d="M3.5 2.5 L5 4 L4.3 5 Q5.3 6.8 7 7.7 L8 7 L9.5 8.5 L8.6 9.5 Q5 9 2.5 3.4 Z" fill="#fff"/>
        </svg>
        <span>(210) 555-0147</span>
      </div>
      <div class="contact-row">
        <svg width="12" height="12" viewBox="0 0 12 12" aria-hidden="true">
          <rect width="12" height="12" fill="var(--brand-orange)"/>
          <path d="M6 2 A2.6 2.6 0 0 1 8.6 4.6 Q8.6 6.5 6 10 Q3.4 6.5 3.4 4.6 A2.6 2.6 0 0 1 6 2 Z" fill="#fff"/>
          <circle cx="6" cy="4.6" r="1" fill="var(--brand-orange)"/>
        </svg>
        <span>4810 E Harlow Ridge Rd<br>Suite 417<br>San Antonio, TX 78163</span>
      </div>
    </div>
  </section>

  <section class="card card-front">
    <div class="brand">
      <span class="brand-square"></span>
      <span class="brand-name">Brightwick Gadget Clinic</span>
    </div>
  </section>
</main>
</body>
</html>
```